Redesign of business card for Cedar Ridge Mechanical

We are looking for a new design for our business cards for Cedar Ridge Mechanical. We are a plumbing & HVAC construction company, operating on the West Coast of Canada and USA. Logo attached.
Industry/Entity Type
Construction - Plumbing & HVAC
Contact Information for Business Card
Name, address, phone numbers, email, website address
Look and feel
Each slider illustrates characteristics of the customer's brand and the style your logo design should communicate.

```html
<!DOCTYPE html>
<html lang="en">
<head>
<meta charset="utf-8">
<title>Cedar Ridge Mechanical — Business Card</title>
<link href="https://fonts.googleapis.com/css2?family=Poppins:wght@300;400;600;700&display=swap" rel="stylesheet">
<style>
  :root {
    --stage: #222223;
    --card: #1e1e20;
    --ink: #ffffff;
    --ink-soft: #d9d9d9;
    --rule: #bdbdbd;
    --pattern-a: #262628;
    --pattern-b: #1a1a1c;
  }
  * { box-sizing: border-box; margin: 0; padding: 0; }
  html, body { width: 1200px; height: 780px; overflow: hidden; }
  body {
    background: var(--stage);
    font-family: "Poppins", sans-serif;
    color: var(--ink);
    display: flex;
    align-items: center;
    justify-content: center;
    gap: 40px;
  }
  .card {
    position: relative;
    width: 520px;
    height: 300px;
    background: var(--card);
    border-radius: 4px;
    overflow: hidden;
    box-shadow: 0 10px 30px rgba(0,0,0,.45);
  }

  /* Front */
  .brand {
    position: absolute;
    left: 30px; top: 28px;
    display: flex; align-items: center; gap: 10px;
  }
  .brand-mark { width: 16px; height: 16px; background: var(--ink); }
  .brand-name {
    font-size: 15px; font-weight: 600; letter-spacing: .3px;
    text-transform: uppercase;
  }
  .contacts {
    position: absolute; left: 30px; top: 66px;
    list-style: none; font-size: 10.5px; font-weight: 300;
    color: var(--ink-soft); line-height: 17px;
  }
  .contacts li { display: flex; align-items: center; gap: 7px; }
  .contacts svg { width: 10px; height: 10px; fill: var(--ink); flex: none; }
  .person {
    position: absolute; right: 36px; top: 108px; text-align: right;
  }
  .person-name { font-size: 24px; font-weight: 300; line-height: 1.1; }
  .person-name strong { font-weight: 700; }
  .person-title { font-size: 11px; font-weight: 400; color: var(--ink-soft); margin-top: 2px; }
  .edge-bar {
    position: absolute; right: 0; top: 110px; width: 12px; height: 44px; background: var(--ink);
  }
  .divider {
    position: absolute; left: 90px; right: 70px; top: 175px; height: 1px; background: var(--rule);
  }
  .address {
    position: absolute; right: 36px; top: 196px; text-align: right;
    font-size: 12.5px; font-weight: 400; line-height: 19px;
  }
  .swoosh { position: absolute; left: 0; bottom: 0; width: 520px; height: 300px; }

  /* Back */
  .pattern-field {
    position: absolute; inset: 0;
    background: linear-gradient(135deg, var(--pattern-a), var(--pattern-b));
  }
  .back-brand {
    position: absolute; inset: 0;
    display: flex; align-items: center; justify-content: center; gap: 14px;
  }
  .back-brand .brand-mark { width: 26px; height: 26px; }
  .back-brand .brand-name { font-size: 26px; font-weight: 600; }
</style>
</head>
<body>

  <section class="card card-front" aria-label="Card front">
    <svg class="swoosh" viewBox="0 0 520 300" aria-hidden="true">
      <path d="M0 228 C 70 232, 150 262, 220 300 L 0 300 Z" fill="#ffffff"/>
      <path d="M0 212 C 90 214, 190 250, 262 300" fill="none" stroke="#ffffff" stroke-width="2.5"/>
      <path d="M0 244 C 60 250, 120 272, 170 300" fill="none" stroke="#1e1e20" stroke-width="3"/>
    </svg>

    <div class="brand">
      <span class="brand-mark"></span>
      <span class="brand-name">Cedar Ridge Mechanical</span>
    </div>

    <ul class="contacts">
      <li>
        <svg viewBox="0 0 24 24"><path d="M6.6 10.8a15.1 15.1 0 0 0 6.6 6.6l2.2-2.2a1 1 0 0 1 1-.25 11.4 11.4 0 0 0 3.6.57 1 1 0 0 1 1 1V20a1 1 0 0 1-1 1A17 17 0 0 1 3 4a1 1 0 0 1 1-1h3.5a1 1 0 0 1 1 1c0 1.25.2 2.45.57 3.57a1 1 0 0 1-.25 1z"/></svg>
        (604) 555-0187
      </li>
      <li>
        <svg viewBox="0 0 24 24"><path d="M2 5h20v14H2z M2 5l10 8 10-8" fill="none" stroke="#fff" stroke-width="2.4"/></svg>
        info@cedarridgemech.com
      </li>
      <li>
        <svg viewBox="0 0 24 24"><circle cx="12" cy="12" r="9" fill="none" stroke="#fff" stroke-width="2.4"/><path d="M3 12h18M12 3c3 3 3 15 0 18M12 3c-3 3-3 15 0 18" fill="none" stroke="#fff" stroke-width="1.8"/></svg>
        www.cedarridgemech.com
      </li>
    </ul>

    <div class="person">
      <p class="person-name"><strong>Marta</strong> Kovacs</p>
      <p class="person-title">Founder &amp; CEO</p>
    </div>
    <span class="edge-bar"></span>

    <span class="divider"></span>

    <address class="address" style="font-style:normal">
      1840 Harbor Ln. Suite 310<br>
      Portland, OR 97209
    </address>
  </section>

  <section class="card card-back" aria-label="Card back">
    <div class="pattern-field" role="img" aria-label="Repeating faint brand pattern across the card background"></div>
    <div class="back-brand">
      <span class="brand-mark"></span>
      <span class="brand-name">Cedar Ridge Mechanical</span>
    </div>
  </section>

</body>
</html>
```